Meridale Bed Company Needs Business Card

Looking for a very nice looking business card. Creative but not extravagant. We sell beds and pillows across the U.S. and need something professional but catchy. I have attached the logo.

Name : Devin Holt
Title : President
Phone : (800) 471-2960
Email: sleep@quilmora.com
Website: www.quilmora.com

Can be single-sided or double-sided
horizontal or vertical

Can use Blues/Greys

Target Market(s)

Mass Market

Industry/Entity Type

Retail

Contact Information for Business Card

Name : Devin Holt
Title : President
Phone : (800) 471-2960
Email: sleep@quilmora.com
Website: www.quilmora.com

Requirements
Must have
• Clean, Modern, Smooth
• Can use Blues/Greys
• On the other side without the information - have something simple like www.quilmora.com or our logo
Nice to have
• Surprise me
Should not have
• Nothing crazy, nothing cluttered

```html
<!DOCTYPE html>
<html lang="en">
<head>
<meta charset="utf-8">
<title>Quilmora Business Card</title>
<link href="https://fonts.googleapis.com/css2?family=Quicksand:wght@300;500;600&display=swap" rel="stylesheet">
<style>
  :root {
    --canvas: #efefef;
    --card-white: #f8f8f8;
    --brand-blue: #2f90cb;
    --brand-blue-light: #3aa0d6;
    --ink: #1f1f1f;
    --on-blue: #f2f7fb;
  }
  * { margin: 0; padding: 0; box-sizing: border-box; }
  html, body {
    width: 1200px; height: 800px; overflow: hidden;
    background: var(--canvas);
    font-family: "Quicksand", sans-serif;
  }
  .stage {
    width: 1200px; height: 800px;
    display: flex; align-items: center; justify-content: center; gap: 60px;
  }
  .card {
    width: 520px; height: 297px; position: relative;
    box-shadow: 0 6px 18px rgba(0,0,0,0.12);
  }
  .card--front { background: var(--card-white); }
  .card--back {
    background: linear-gradient(160deg, var(--brand-blue) 0%, var(--brand-blue-light) 100%);
  }
  .wordmark {
    font-family: "Quicksand", sans-serif;
    font-weight: 300;
    letter-spacing: 4px;
    line-height: 1;
  }
  .card--front .wordmark {
    position: absolute; left: 44px; top: 48px;
    font-size: 44px; color: var(--brand-blue);
  }
  .contact {
    position: absolute; right: 44px; bottom: 40px; width: 230px;
    color: var(--ink);
  }
  .contact__name { font-size: 22px; font-weight: 500; letter-spacing: 0.5px; }
  .contact__title {
    font-size: 14px; font-weight: 600; color: var(--brand-blue);
    margin: 2px 0 10px;
  }
  .contact__row {
    display: flex; align-items: center; gap: 8px;
    font-size: 14px; font-weight: 500; margin-top: 4px;
  }
  .contact__icon { width: 13px; height: 13px; flex: none; }
  .card--back .wordmark {
    position: absolute; left: 140px; top: 96px;
    font-size: 64px; color: var(--on-blue);
  }
  .card--back .site {
    position: absolute; left: 146px; top: 186px;
    font-size: 13px; font-weight: 500; letter-spacing: 1px;
    color: var(--on-blue);
  }
</style>
</head>
<body>
<main class="stage">
  <section class="card card--front">
    <div class="wordmark">quilmora</div>
    <div class="contact">
      <div class="contact__name">Devin Holt</div>
      <div class="contact__title">President</div>
      <div class="contact__row">
        <svg class="contact__icon" viewBox="0 0 16 16" aria-hidden="true">
          <rect width="16" height="16" rx="3" fill="#2f90cb"/>
          <path d="M5 3.5l1.6 2.2-1 1.2c.7 1.5 1.8 2.6 3.3 3.3l1.2-1 2.2 1.6-.8 1.9C7.6 12.6 3.4 8.4 3.1 4.3z" fill="#fff"/>
        </svg>
        <span>(800) 471-2960</span>
      </div>
      <div class="contact__row">
        <svg class="contact__icon" viewBox="0 0 16 16" aria-hidden="true">
          <rect width="16" height="16" rx="3" fill="#2f90cb"/>
          <rect x="3" y="5" width="10" height="7" fill="none" stroke="#fff" stroke-width="1.2"/>
          <path d="M3 5l5 4 5-4" fill="none" stroke="#fff" stroke-width="1.2"/>
        </svg>
        <span>sleep@quilmora.com</span>
      </div>
      <div class="contact__row">
        <svg class="contact__icon" viewBox="0 0 16 16" aria-hidden="true">
          <circle cx="8" cy="8" r="7.5" fill="#2f90cb"/>
          <circle cx="8" cy="8" r="5" fill="none" stroke="#fff" stroke-width="1"/>
          <ellipse cx="8" cy="8" rx="2.2" ry="5" fill="none" stroke="#fff" stroke-width="1"/>
          <path d="M3 8h10" stroke="#fff" stroke-width="1"/>
        </svg>
        <span>www.quilmora.com</span>
      </div>
    </div>
  </section>
  <section class="card card--back">
    <div class="wordmark">quilmora</div>
    <div class="site">www.quilmora.com</div>
  </section>
</main>
</body>
</html>
```